Events Company Needs Website Revamp

Tallwood Expos is an events company that specializes in organizing and marketing large scale consumer and trade events globally.

The new web design should provide easy classification of the events, and allow visitors to find and access the details page within 2 clicks.

There are no strict guidelines on the color theme. It just has to blend naturally with the corporate logo.
Updates

The company logo is uploaded (pdf & ai)

I came across this design which I like very much. Elegant and corporate with nice modern fonttype.

Layout wise, neat and clear. 

Please see how you can emulate the design further. Particularly, highlighting the 2 event arms (Trade/Consumer) clearly.

Target Market(s)

Consumer looking for upcoming events, B2C companies looking to participate, B2B companies looking to connect with other companies

Industry/Entity Type

It Company

Requirements
Must have
• The new design should help to achieve the following objectives:
1) Visitors should be able to easily identify and access the 2 different types of events (i.e. Trade Events and Consumer Events).
2) Visitors should be able to easily find events that interest them (e.g. filter by date, trade or consumer, category [i.e. beauty, retail, F&B, construction, etc.]).
3) Visitors should be able to access an event’s details page within 2 clicks from any page.

Main navigation to include the following links:
- About Us
- Calendar
- Consumer Events
- Trade Events
- Contact Us

Design for Three (3) pages required:
A. Homepage
- Clear differentiation and easy access to the 2 different types of events (trade and consumer)
- Featured area to showcase latest 4-5 events
- Quick way to access events calendar
- Clear call-to-action for newsletter signup
- Social media sharing widgets/buttons
- A section for latest news and press releases
- A section for featured testimonials

B. Events Listing Page
- List of links to all events
- Logos and/or photos of events
- Filter / tags to find events in a specific category (e.g. food, electronics, building & construction, etc.)

C. Events Details Page
- Photo strip to showcase event photos / brochure
- A section with event details (Date, Venue, Event Description, etc.)
- Call-to-action button to visit event website
- Call-to-action button to contact event sales team
- E.g. http://vantly-demo.com/user/brightfoxhk/brightfox-monday-2011 but with the photo strip permanently extended and of a shorter height. Event details and call-to-action buttons should also be easily seen

```html
<!DOCTYPE html>
<html lang="en">
<head>
<meta charset="utf-8">
<title>Tallwood Expos</title>
<link rel="stylesheet" href="https://fonts.googleapis.com/css2?family=Open+Sans:wght@400;600;700&display=swap">
<style>
:root{
  --brown-dark:#5a2c0f;
  --brown:#8a4513;
  --brown-bar:#a6520f;
  --orange:#f47a1f;
  --orange-light:#f9b233;
  --peach:#fbd8bd;
  --peach-light:#fde6d4;
  --red:#d7192f;
  --ink:#333;
  --ink-soft:#555;
  --grey-band:#e2e2e2;
  --panel-top:#e9e9e9;
  --panel-bottom:#f7f7f7;
  --white:#fff;
}
*{box-sizing:border-box;margin:0;padding:0}
html,body{width:1170px;height:1200px;overflow:hidden}
body{position:relative;background:var(--white);font-family:"Open Sans",Arial,sans-serif;color:var(--ink)}
.abs{position:absolute}

/* header */
.topbar{left:0;top:0;width:1170px;height:60px;background:linear-gradient(#6a3512,#9a5018)}
.main-nav{left:356px;top:8px;height:52px;display:flex;list-style:none}
.main-nav li{height:52px;line-height:50px;font-size:14px;color:#fff;padding:0 27px}
.main-nav li.current{background:var(--peach-light);color:var(--ink);width:118px;text-align:center;padding:0}
.hero{left:0;top:60px;width:1170px;height:417px;background:linear-gradient(#fbd6b8,#fcdcc4)}
.bubble{border-radius:50%;background:rgba(255,255,255,.25)}
.brand-disc{left:165px;top:4px;width:168px;height:168px;border-radius:50%;background:var(--peach-light)}
.brand{left:200px;top:92px;display:flex;align-items:center;gap:8px;white-space:nowrap}
.brand-dot{width:13px;height:13px;border-radius:50%;background:var(--orange)}
.brand-name{font-size:23px;font-weight:600;color:#3a2a22}
.parent{left:202px;top:178px;font-size:14px;color:#2a5a9e;white-space:nowrap}
.welcome{left:148px;top:244px;font-size:25px;line-height:29px;font-weight:400;color:#333}
.welcome b{font-weight:700}
.intro{left:150px;top:317px;width:262px;font-size:11.8px;line-height:15px;letter-spacing:-.1px;text-align:justify;color:#444}
.hero-more{left:351px;top:421px;font-size:12px;color:#333}
.slide-frame{left:436px;top:86px;width:571px;height:361px;background:#fff;box-shadow:0 1px 6px rgba(0,0,0,.25)}
.slide-photo{left:443px;top:93px;width:557px;height:348px;background:linear-gradient(160deg,#d6d6d6,#8b8b8b 55%,#4a4a4a)}
.slide-arrow{width:26px;height:40px;top:252px;background:rgba(215,25,47,.6)}
.dots{left:720px;top:459px;display:flex;gap:5px}
.dots span{width:10px;height:10px;border-radius:50%;background:#eee;border:1px solid #ccc}
.dots .on{background:var(--red);border-color:var(--red)}

/* event cards */
.band{left:0;top:477px;width:1170px;height:140px;background:var(--grey-band)}
.card{top:515px;height:150px;background:#fff}
.card h2{position:absolute;left:15px;top:8px;font-size:18px;font-weight:400;color:#333}
.card h2 em{font-style:normal;color:var(--red)}
.card p{position:absolute;font-size:9.5px;line-height:12.2px;color:#444;text-align:justify}
.card p.details{font-size:9px;line-height:16.5px;text-align:left;color:#666;white-space:nowrap}
.card p.details b{color:#333;font-weight:600}
.card-foot{position:absolute;left:0;bottom:0;width:100%;height:29px;background:var(--orange);color:#fde3c8;font-size:8.5px;line-height:29px;padding:0 14px;display:flex;justify-content:space-between}
.logo-slot{position:absolute}

/* panels */
.panel{top:678px;width:291px;height:312px;border-radius:10px;background:linear-gradient(var(--panel-top),var(--panel-bottom));box-shadow:0 1px 3px rgba(0,0,0,.15)}
.panel h3{position:absolute;left:55px;top:14px;font-size:16px;font-weight:400;color:#333}
.panel h3 em{font-style:normal;color:var(--red)}
.panel-icon{position:absolute;left:12px;top:8px;width:32px;height:34px;border-radius:4px;background:#fff;border:1px solid #bbb}
.rule{position:absolute;left:8px;width:275px;height:1px;background:#d8d8d8}
.entry{position:absolute;left:14px;width:262px;font-size:11.8px;line-height:16.5px;text-align:justify;color:#333}
.byline{position:absolute;right:22px;font-size:11.5px;color:#333}
.byline em{font-style:normal;color:var(--red);font-size:13px}
.panel-more{position:absolute;left:10px;top:290px;width:271px;height:24px;background:var(--brown-bar);color:var(--orange-light);font-size:12px;line-height:24px;text-align:right;padding-right:30px}
.panel-more::after{content:"";position:absolute;right:12px;top:8px;width:6px;height:6px;border-top:2px solid #fff;border-right:2px solid #fff;transform:rotate(45deg)}

.signup-title{left:791px;top:686px;font-size:17px;color:#333;letter-spacing:.3px}
.signup-title em{font-style:normal;color:var(--red)}
.email{left:755px;top:722px;width:220px;height:28px;border-radius:6px;background:#fff;font-size:13px;color:#999;padding:5px 10px}
.go{left:988px;top:725px;font-size:20px;font-weight:700;color:#9a5a17}
.cal-title{left:786px;top:765px;font-size:17px;color:#333;letter-spacing:.3px}
.calendar{left:762px;top:800px;width:248px;height:178px;border-radius:4px;background:var(--orange-light);box-shadow:0 0 0 3px #fff,0 1px 4px rgba(0,0,0,.3)}
.cal-head{height:26px;background:linear-gradient(#f8a21e,#e98a0f);color:#fff;font-size:11px;text-align:center;line-height:26px}
.cal-days{display:grid;grid-template-columns:repeat(7,1fr);background:#d9771a;color:#fbd08d;font-size:10.5px;text-align:center;height:18px;line-height:18px}
.cal-grid{display:grid;grid-template-columns:repeat(7,29px);gap:3px 3px;padding:6px 8px;font-size:11px;text-align:center}
.cal-grid span{height:16px;line-height:16px;background:#fbc35c;color:#222}
.cal-grid .off{color:#fff;background:#fac05a}
.cal-grid .hi{color:#fff;font-weight:700}
.cal-grid .today{background:#fff}

/* connect */
.connect{left:627px;top:1008px;font-size:15px;color:#222}
.social-tab{left:598px;top:1035px}
.social{top:1046px;width:22px;height:22px;border-radius:3px}

/* footer */
.footer{left:0;top:1077px;width:1170px;height:123px;background:linear-gradient(#5e2f10,#9a5119)}
.foot-nav{left:144px;top:1091px;display:flex;gap:23px;list-style:none;font-size:10.5px;color:#fff}
.copyright{left:0;top:1142px;width:1170px;text-align:center;font-size:9px;color:#fff}
</style>
</head>
<body>

<header>
  <div class="abs topbar"></div>
  <div class="abs hero"></div>
  <div class="abs bubble" style="left:118px;top:360px;width:70px;height:70px"></div>
  <div class="abs bubble" style="left:133px;top:160px;width:20px;height:20px"></div>
  <div class="abs bubble" style="left:390px;top:135px;width:36px;height:36px"></div>
  <div class="abs bubble" style="left:150px;top:90px;width:30px;height:30px"></div>
  <div class="abs brand-disc"></div>
  <div class="abs brand"><span class="brand-dot"></span><span class="brand-name">Tallwood Expos</span></div>
  <div class="abs parent">A SUBSIDIARY OF Northgate Media</div>
  <ul class="abs main-nav">
    <li class="current">About Us</li><li>Calendar</li><li>Consumer Events</li><li>Trade Events</li><li>Contact us</li>
  </ul>
  <h1 class="abs welcome"><b>Welcome to</b><br>Tallwood Expos</h1>
  <p class="abs intro">Being at the right place at the right time can spell success for your business. And Tallwood Expos links you to a dimension of immense possibilities, where people and ideas converge to create great shows and events to bring out the best in your business.</p>
  <div class="abs hero-more">Read more</div>
  <div class="abs slide-frame"></div>
  <div class="abs slide-photo" role="img" aria-label="Photo of an exhibition hall with fashion stands, mannequins and visitors"></div>
  <div class="abs slide-arrow" style="left:443px;border-radius:0 20px 20px 0"></div>
  <div class="abs slide-arrow" style="left:974px;border-radius:20px 0 0 20px"></div>
  <div class="abs dots"><span></span><span></span><span class="on"></span></div>
</header>

<section>
  <div class="abs band"></div>

  <article class="abs card" style="left:138px;width:295px">
    <h2>Trade <em>Event</em></h2>
    <div class="logo-slot" style="left:18px;top:40px;width:70px;height:70px;border-radius:50%;background:var(--red)" role="img" aria-label="Trade fair badge"></div>
    <p style="left:107px;top:36px;width:176px">Held in conjunction with Northbay Fair is Stationery &amp; DeskLine (DLFair), a showcase of office products, business solutions and stationery supplies. The Event is an emergence of a powerful combination providing greater exposure</p>
    <div class="card-foot"><span>Date: 20 - 22 July 2011 , Wednesday - Friday</span><span>Read more &#8250;</span></div>
  </article>

  <article class="abs card" style="left:439px;width:293px">
    <h2>Consumer <em>Event</em></h2>
    <div class="logo-slot" style="left:12px;top:46px;width:80px;height:40px;background:var(--orange)" role="img" aria-label="Children's academy event logo"></div>
    <p style="left:104px;top:36px;width:176px">The Little Owls Academy is a one stop edutainment hub which focuses on holistic learning and development programmes and services for children aged 0 – 12 years old. It endeavours to be an exciting and fulfilling 3-day event</p>
    <div class="card-foot"><span>Date: 16 - 18 March 2012 , Friday - Sunday</span><span>Read more &#8250;</span></div>
  </article>

  <article class="abs card" style="left:737px;width:293px">
    <h2>Latest <em>Event</em></h2>
    <div class="logo-slot" style="left:12px;top:66px;width:70px;height:16px;background:#ccc" role="img" aria-label="Technology showcase event logo"></div>
    <p class="details" style="left:88px;top:41px"><b>Venue :</b> Harbor Hall @ Lumen Park, Singapore 30<br>Lumen Park Street, Singapore S100214<br><b>Date :</b> 29 February 2012 - 02 December 2011<br><b>Time :</b> 09:00 - 20:00</p>
    <div class="card-foot"><span>Date: 16 - 18 March 2012 , Friday - Sunday</span><span>Read more &#8250;</span></div>
  </article>
</section>

<section>
  <div class="abs panel" style="left:137px">
    <div class="panel-icon"></div>
    <h3>Latest <em>News</em></h3>
    <div class="rule" style="top:43px"></div>
    <p class="entry" style="top:58px">21 jan 2012 : Lorem Ipsum is simply dummy text of the printing and typesetting industry. Lorem Ipsum has been the industry's standard dummy text ever since</p>
    <div class="rule" style="top:131px"></div>
    <p class="entry" style="top:141px">21 jan 2012 : Lorem Ipsum is simply dummy text of the printing and typesetting industry. Lorem Ipsum has been the industry's standard dummy text ever since</p>
    <div class="rule" style="top:214px"></div>
    <p class="entry" style="top:222px">21 jan 2012 : Lorem Ipsum is simply dummy text of the printing and typesetting industry. Lorem Ipsum has been the industry's standard dummy text ever since</p>
    <div class="panel-more">Read more</div>
  </div>

  <div class="abs panel" style="left:439px">
    <div class="panel-icon" style="width:26px"></div>
    <h3 style="left:50px;top:12px">Testimonials</h3>
    <div class="rule" style="top:43px"></div>
    <p class="entry" style="top:58px">21 jan 2012 : Lorem Ipsum is simply dummy text of the printing and typesetting industry. Lorem Ipsum</p>
    <div class="byline" style="top:105px">By <em>Lorem Ipsum</em></div>
    <div class="rule" style="top:131px"></div>
    <p class="entry" style="top:141px">21 jan 2012 : Lorem Ipsum is simply dummy text of the printing and typesetting industry. Lorem Ipsum</p>
    <div class="byline" style="top:188px">By <em>Lorem Ipsum</em></div>
    <div class="rule" style="top:214px"></div>
    <p class="entry" style="top:220px">21 jan 2012 : Lorem Ipsum is simply dummy text of the printing and typesetting industry. Lorem Ipsum</p>
    <div class="byline" style="top:267px">By <em>Lorem Ipsum</em></div>
    <div class="panel-more">Read more</div>
  </div>

  <div class="abs panel" style="left:740px"></div>
  <svg class="abs" style="left:753px;top:684px" width="32" height="30" viewBox="0 0 32 30" aria-hidden="true">
    <rect x="2" y="8" width="26" height="18" rx="2" fill="#f2b33a" transform="rotate(-15 15 17)"/>
    <path d="M4 10 L16 19 L28 5" fill="none" stroke="#c9831b" stroke-width="1.5" transform="rotate(-5 15 17)"/>
  </svg>
  <div class="abs signup-title">Sign up For a <em>Newsletter</em></div>
  <div class="abs email">enter your email id</div>
  <div class="abs go">Go</div>
  <svg class="abs" style="left:752px;top:765px" width="28" height="26" viewBox="0 0 28 26" aria-hidden="true">
    <rect x="3" y="4" width="22" height="19" rx="2" fill="#fff" stroke="#5577aa" stroke-width="1.5" transform="rotate(-12 14 14)"/>
    <line x1="6" y1="10" x2="23" y2="6" stroke="#5577aa" stroke-width="2"/>
  </svg>
  <div class="abs cal-title">Events Calendar</div>
  <svg class="abs" style="left:934px;top:769px" width="32" height="18" viewBox="0 0 32 18" aria-hidden="true">
    <path d="M2 2 L10 9 L2 16 M16 2 L24 9 L16 16" fill="none" stroke="#ccc" stroke-width="3"/>
  </svg>
  <div class="abs calendar">
    <div class="cal-head">December 2009</div>
    <div class="cal-days"><span>Su</span><span>Mo</span><span>Tu</span><span>We</span><span>Th</span><span>Fr</span><span>Sa</span></div>
    <div class="cal-grid">
      <span class="off">25</span><span class="off">26</span><span class="off">27</span><span class="off">28</span><span class="off">29</span><span class="off">30</span><span>1</span>
      <span>2</span><span>3</span><span>4</span><span>5</span><span>6</span><span>7</span><span>8</span>
      <span>9</span><span>10</span><span>11</span><span>12</span><span>13</span><span class="hi">14</span><span>15</span>
      <span>16</span><span>17</span><span>18</span><span>19</span><span>20</span><span class="today">21</span><span>22</span>
      <span>23</span><span>24</span><span>25</span><span>26</span><span>27</span><span>28</span><span>29</span>
      <span>30</span><span class="off">1</span><span class="off">2</span><span class="off">3</span><span class="off">4</span><span class="off">5</span><span class="off">6</span>
    </div>
  </div>
</section>

<section>
  <div class="abs connect">Connect us on :</div>
  <svg class="abs social-tab" width="412" height="42" viewBox="0 0 412 42" aria-hidden="true">
    <defs><linearGradient id="tabShade" x1="0" y1="0" x2="0" y2="1"><stop offset="0" stop-color="#f2f2f2"/><stop offset="1" stop-color="#d6d6d6"/></linearGradient></defs>
    <path d="M0 42 Q12 2 40 2 H372 Q400 2 412 42 Z" fill="url(#tabShade)"/>
  </svg>
  <div class="abs social" style="left:657px;background:#333" role="img" aria-label="Social network link"></div>
  <div class="abs social" style="left:729px;background:#4fb0e0" role="img" aria-label="Social network link"></div>
  <div class="abs social" style="left:794px;background:#3b5998" role="img" aria-label="Social network link"></div>
  <div class="abs social" style="left:863px;background:#f07a1c" role="img" aria-label="Social network link"></div>
  <div class="abs social" style="left:923px;background:#2a8bc6" role="img" aria-label="Social network link"></div>
</section>

<footer>
  <div class="abs footer"></div>
  <ul class="abs foot-nav"><li>About Us</li><li>Calendar</li><li>Consumer Events</li><li>Trade Events</li><li>Contact us</li></ul>
  <div class="abs copyright">©2012 Tallwood Expos, All Rights Reserved</div>
</footer>

</body>
</html>
```